velorimo.gr wordpress makeover

We need a makeover of our wordpress website velorimo.gr We are a company that provides astrology services via phone either by billable phone number or by prepaid packages.This is what we sell. Moreover, we share everyday astrology related articles to our blog. It will be a multy page website. Our goal is always to sell our phone prepaid packages or to make the visitor of the website call our billable numbers. Our website should have:
-a home page introducing its content (astrologers, call packages, blog section with categories).
-astrologers page (you can see the existing one to understand)
-Phone packages page (eshop page where you can buy prepaid phone packages. woo commerce maybe)
- Blog page divined by categories.
The website should have places for display banners eg. a sidebar.
I will provide some screen shots of websites we like. You can always visit our existing website www.velorimo.gr to see it for yourself.

Target Market(s)

people seeking for future telling - astrologer services via phone. People who like to be informed about everyday astrology predictions

Industry/Entity Type

Astrology - tarot services via phone

Coding

Coded - Design and coding required

Number of Pages Required

5+ page

Font styles to use
Decorative
Script

Colors
6B429C
8869AF
B7A5CE
E3DAEB
F3F0F8

Requirements
Must have
• -Home page -Astrologers page -Phone packages page (eshop) -Blog page with categories - Made following the guidelines of quenbly so as to be efficient in quenbly ads marketing. Mobile friendly.
Nice to have
• Nice call to action buttons to call or buy packages. Sidebar with banner ads of maybe our offers.

```html
<!DOCTYPE html>
<html lang="en">
<head>
<meta charset="utf-8">
<title>velorimo.gr — Astrology by phone</title>
<link href="https://fonts.googleapis.com/css2?family=Open+Sans:wght@400;600;700&family=Playfair+Display:ital,wght@1,700;1,900&family=Libre+Baskerville:wght@400;700&display=swap" rel="stylesheet">
<style>
:root{
  --purple:#6B429C;
  --purple-mid:#8869AF;
  --lilac:#B7A5CE;
  --lilac-light:#E3DAEB;
  --mist:#F3F0F8;
  --card:#7a4aa8;
  --pill:#ecc7ef;
  --pill-text:#4e2a7a;
  --nav-blue:#1aa3e2;
  --navy:#0b0f2e;
  --teal:#22b4c9;
  --green:#1e9b3a;
  --white:#ffffff;
}
*{box-sizing:border-box;margin:0;padding:0}
html,body{width:1200px;height:3379px;overflow:hidden}
body{font-family:"Open Sans",sans-serif;color:var(--white);
  background:linear-gradient(180deg,#1b2358 0%,#0c1233 20%,#12183c 40%,#1a1440 55%,#0e1234 70%,#161a48 85%,#0b0e2a 100%);}
.page{position:relative;width:1200px;height:3379px;overflow:hidden}
.abs{position:absolute}

/* header */
.site-header{position:absolute;top:0;left:0;width:1200px;height:116px;background:var(--white)}
.brand{position:absolute;left:104px;top:42px;font-size:23px;font-weight:600;color:#1b1b2a;display:flex;align-items:center;gap:6px}
.brand i{display:block;width:12px;height:12px;border-radius:50%;background:#9a9a9a}
.brand-mark{position:absolute;left:100px;top:113px;width:44px;height:3px;background:var(--purple)}
.main-nav a{position:absolute;top:42px;font-size:25px;color:#2a2a2a;text-decoration:none}
.header-badge{position:absolute;left:770px;top:32px;font-size:34px;font-weight:700;color:#2f3da8}
.zodiac-nav{position:absolute;top:116px;left:0;width:1200px;height:52px;background:var(--nav-blue);display:flex;align-items:center;padding-left:100px;gap:18px}
.zodiac-nav a{font-size:15px;color:var(--white);text-decoration:none;letter-spacing:.5px}
.lang{margin-left:6px;width:88px;height:34px;border-radius:17px;background:#5a2aa8;display:flex;align-items:center;justify-content:center;gap:8px;font-size:17px}
.lang:after{content:"";border:6px solid transparent;border-top-color:#fff;margin-top:6px}

/* hero */
.hero-art{position:absolute;left:650px;top:168px;width:550px;height:600px;
  background:radial-gradient(circle at 50% 32%,#e8f1ff 0,#7fb0f0 8%,#2a4aa8 28%,rgba(20,30,80,0) 60%)}
.hero-fade{position:absolute;left:0;top:168px;width:1200px;height:600px;
  background:radial-gradient(ellipse at 70% 40%,rgba(60,90,180,.55),rgba(10,14,40,0) 65%),linear-gradient(180deg,rgba(40,55,120,.6),rgba(10,14,40,.1))}
.welcome{position:absolute;left:109px;top:270px;font-family:"Playfair Display",serif;font-style:italic;font-weight:700;font-size:38px}
.hero-title{position:absolute;left:96px;top:305px;font-family:"Playfair Display",serif;font-style:italic;font-weight:900;font-size:118px;line-height:1}
.hero-text{position:absolute;left:98px;top:456px;width:530px;font-size:15px;line-height:26px}
.btn{position:absolute;border-radius:30px;background:var(--pill);color:var(--pill-text);font-size:21px;display:flex;align-items:center;justify-content:center;text-decoration:none}
.mini-post{position:absolute;display:flex;gap:14px;top:629px}
.mini-post .thumb{width:101px;height:87px;border-radius:6px}
.mini-post h4{font-size:16px;font-weight:600;line-height:22px;width:210px;margin-top:6px}
.mini-post p{font-size:17px;margin-top:4px}
.t-tarot{background:linear-gradient(135deg,#c9a98a,#8a5a3a 60%,#d8c3b0)}
.t-lady{background:linear-gradient(135deg,#3a7fd6,#e7d7ef 60%,#7ac0e0)}
.t-cloud{background:radial-gradient(circle at 55% 45%,#fff 0,#cfd8f5 14%,#2d3aa0 38%,#1f2b86)}
.t-cups{background:linear-gradient(135deg,#f3b04a,#3aa1c8 45%,#c83a2a 80%)}

/* section titles */
.section-title{position:absolute;left:0;width:1200px;text-align:center;font-family:"Libre Baskerville",serif;font-weight:700;font-size:44px;letter-spacing:-.5px}

/* astrologers */
.astro-card{position:absolute;top:912px;width:493px;height:459px;background:var(--card);border-radius:10px}
.astro-photo{position:absolute;left:9px;top:9px;width:475px;height:256px;border-radius:4px}
.astro-card h3{position:absolute;left:16px;top:284px;font-family:"Libre Baskerville",serif;font-weight:700;font-size:29px}
.astro-card p{position:absolute;left:18px;top:336px;width:440px;font-family:"Libre Baskerville",serif;font-size:12.5px;line-height:26px;color:#f1e8f8}
.call-pill{position:absolute;width:223px;height:73px;border-radius:37px;background:var(--white);display:flex;align-items:center;justify-content:center;gap:6px}
.call-pill small{color:#222;font-size:12px;line-height:12px;text-align:center}
.call-pill b{background:var(--green);color:#fff;font-size:28px;padding:0 6px 0 14px;border-radius:6px;display:flex;align-items:center;gap:6px}
.call-pill b i{font-style:normal;font-size:13px;background:#111;border-radius:50%;width:22px;height:22px;display:flex;align-items:center;justify-content:center}

/* packages */
.package{position:absolute;top:1695px;width:325px;height:353px;border-radius:10px;overflow:hidden}
.package .price{position:absolute;left:0;width:100%;text-align:center;top:30px;font-family:"Libre Baskerville",serif;font-weight:700;font-size:72px}
.package .mins{position:absolute;left:0;width:100%;text-align:center;top:130px;font-family:"Libre Baskerville",serif;font-weight:700;font-size:42px}
.ribbon{position:absolute;left:0;top:62px;width:60px;height:230px;background:var(--card);clip-path:polygon(0 12%,100% 0,100% 100%,0 88%)}
.ribbon span{position:absolute;left:8px;bottom:20px;transform:rotate(-90deg);transform-origin:left bottom;white-space:nowrap;margin-left:40px;font-family:"Libre Baskerville",serif;font-weight:700;font-size:31px}
.pk1{background:linear-gradient(180deg,#1d2d6e,#3a4a9a 45%,#d48a5a 80%,#1a1a2a)}
.pk2{background:radial-gradient(circle,#2a4a9a,#152760 70%)}
.pk3{background:linear-gradient(180deg,#2a3a82,#6d8ad0 45%,#c9d4ea 60%,#3a4a78)}

/* blog */
.blog-card{position:absolute;width:315px}
.blog-card .img{height:203px;border-radius:10px;position:relative}
.blog-card .tag{position:absolute;right:14px;top:18px;background:var(--purple);font-family:"Libre Baskerville",serif;font-size:11px;padding:5px 12px;border-radius:12px}
.blog-card h4{font-family:"Libre Baskerville",serif;font-weight:700;font-size:18px;line-height:26px;margin:18px 0 0 13px}
.side-post{position:absolute;left:771px;display:flex;gap:16px}
.side-post .thumb{width:101px;height:87px;border-radius:6px}
.side-post h5{font-size:17px;font-weight:600;line-height:22px;width:220px;margin-top:8px}
.side-post p{font-size:17px;margin-top:6px}

/* footer */
.footer-brand{position:absolute;left:0;width:1200px;top:2980px;text-align:center;font-size:54px;font-weight:600;color:var(--teal)}
.footer-brand i{display:inline-block;width:32px;height:32px;border-radius:50%;background:var(--teal);margin-left:6px;vertical-align:middle}
.footer-links{position:absolute;top:3086px;left:0;width:1200px;display:flex;justify-content:center;gap:64px;font-family:"Libre Baskerville",serif;font-size:23px}
.contact{position:absolute;top:3170px;display:flex;align-items:center;gap:20px;font-family:"Libre Baskerville",serif;font-size:14px;line-height:26px}
.contact .ico{width:60px;height:60px;border-radius:50%;background:#e2a9e0;display:flex;align-items:center;justify-content:center}
.divider{position:absolute;top:3170px;width:1px;height:62px;background:#fff}
.rule{position:absolute;left:80px;top:3274px;width:1000px;border-top:1px dashed #c9c9d8}
.copyright{position:absolute;top:3306px;left:0;width:1200px;text-align:center;font-family:"Libre Baskerville",serif;font-weight:700;font-size:15px}
</style>
</head>
<body>
<div class="page">

<header class="site-header">
  <div class="brand">velorimo<i></i></div>
  <div class="brand-mark"></div>
  <nav class="main-nav">
    <a href="#" style="left:281px">Blog</a>
    <a href="#" style="left:408px">Astrologers</a>
    <a href="#" style="left:614px">Pricing</a>
  </nav>
  <div class="header-badge">velorimo 14877</div>
</header>
<nav class="zodiac-nav">
  <a href="#">ARIES</a><a href="#">TAURUS</a><a href="#">GEMINI</a><a href="#">CANCER</a><a href="#">LEO</a><a href="#">VIRGIN</a><a href="#">LIBRA</a><a href="#">SCORPIO</a><a href="#">SAGITTARIUS</a><a href="#">CAPRICORN</a><a href="#">AQUARIUS</a><a href="#">PISCES</a>
  <span class="lang">EN</span>
</nav>

<section class="hero">
  <div class="hero-fade"></div>
  <div class="hero-art" role="img" aria-label="Glowing zodiac wheel in a starry sky above a person with raised arms"></div>
  <div class="welcome">Welcome To</div>
  <h1 class="hero-title">Velorimo</h1>
  <p class="hero-text">The signs for today 17/11 ARIES You will feel a strong need to withdraw from socializing, and stay in</p>
  <a class="btn" href="#" style="left:101px;top:535px;width:170px;height:59px">Read More</a>
  <article class="mini-post" style="left:97px">
    <div class="thumb t-tarot" role="img" aria-label="Hands laying out tarot cards"></div>
    <div><h4>The zodiac signs for today, Friday 18/11</h4><p>10 hours ago</p></div>
  </article>
  <article class="mini-post" style="left:430px">
    <div class="thumb t-lady" role="img" aria-label="Illustration of a fortune teller with cards"></div>
    <div><h4>Tarot for Today, Thursday 11/17</h4><p>15 hours ago</p></div>
  </article>
</section>

<section class="astrologers">
  <h2 class="section-title" style="top:805px">ASTROLOGERS</h2>
  <article class="astro-card" style="left:89px">
    <div class="astro-photo" role="img" aria-label="Portrait of astrologer Eleni Varkari with call banner" style="background:linear-gradient(120deg,#8a3a2a,#d89a4a 55%,#1a1a1a)"></div>
    <h3>ELENI VARKARI</h3>
    <p><b style="color:#1a0f2a">Astrologer</b> specializing in Astropsychology, with many years of research on human relationships. Call now for a personal astrological forecast. I have the answers to the questions that concern you.</p>
  </article>
  <div class="call-pill" style="left:342px;top:1338px"><small>καλέστε<br>τώρα</small><b>14877<i>24</i></b></div>
  <article class="astro-card" style="left:617px">
    <div class="astro-photo" role="img" aria-label="Portrait of astrologer Dora Melitou with moon backdrop" style="background:linear-gradient(120deg,#2a4ab8,#5a2a8a 55%,#0a0a2a)"></div>
    <h3>DORA MELITOU</h3>
    <p>Powerful psychic. I will help you solve your love and business problems with sure answers through the science of astrology. I am the <b>astrologer</b> you are looking for! A telephone forecast will convince you.</p>
  </article>
  <div class="call-pill" style="left:870px;top:1338px"><small>καλέστε<br>τώρα</small><b>14877<i>24</i></b></div>
  <a class="btn" href="#" style="left:514px;top:1443px;width:170px;height:58px">show More</a>
</section>

<section class="packages">
  <h2 class="section-title" style="top:1584px">CALL PACKAGES</h2>
  <article class="package pk1" role="img" aria-label="Silhouette on a hill under a galaxy">
    <div class="price">30€</div><div class="mins">20 MINS</div>
    <div class="ribbon"><span>talking time</span></div>
  </article>
  <article class="package pk2" style="left:438px" role="img" aria-label="Zodiac chart on deep blue">
    <div class="price">30€</div><div class="mins">20 MINS</div>
    <div class="ribbon"><span>talking time</span></div>
  </article>
  <article class="package pk3" style="left:776px" role="img" aria-label="Person meditating by the sea under a night sky">
    <div class="price">30€</div><div class="mins">20 MINS</div>
    <div class="ribbon"><span>talking time</span></div>
  </article>
  <style>.pk1{left:98px}</style>
  <a class="btn" href="#" style="left:184px;top:2023px;width:170px;height:59px">Read More</a>
  <a class="btn" href="#" style="left:516px;top:2023px;width:170px;height:59px">Read More</a>
  <a class="btn" href="#" style="left:862px;top:2023px;width:170px;height:59px">Read More</a>
</section>

<section class="blog">
  <h2 class="section-title" style="top:2236px">OUR BLOG</h2>
  <article class="blog-card" style="left:96px;top:2339px">
    <div class="img t-tarot" role="img" aria-label="Hands laying out tarot cards"><span class="tag">10 hours ago</span></div>
    <h4>The zodiac signs for today, Friday 18/11</h4>
  </article>
  <article class="blog-card" style="left:431px;top:2339px">
    <div class="img t-lady" role="img" aria-label="Illustration of a fortune teller with cards"><span class="tag">15 hours ago</span></div>
    <h4>Tarot for today, Thursday 11/17</h4>
  </article>
  <article class="blog-card" style="left:96px;top:2628px">
    <div class="img t-cloud" role="img" aria-label="Cloud above a ladder on blue"><span class="tag">10 hours ago</span></div>
    <h4>The zodiac signs for today, Thursday 17/11</h4>
  </article>
  <article class="blog-card" style="left:431px;top:2628px">
    <div class="img t-cups" role="img" aria-label="Watercolour painting of tea cups"><span class="tag">10 hours ago</span></div>
    <h4>Tarot for today, Wednesday 11/16</h4>
  </article>

  <article class="side-post" style="top:2341px"><div class="thumb t-tarot" role="img" aria-label="Tarot cards"></div><div><h5>The zodiac signs for today, Friday 18/11</h5><p>10 hours ago</p></div></article>
  <article class="side-post" style="top:2474px"><div class="thumb t-lady" role="img" aria-label="Fortune teller illustration"></div><div><h5>Tarot for Today, Thursday 11/17</h5><p>15 hours ago</p></div></article>
  <article class="side-post" style="top:2606px"><div class="thumb t-cloud" role="img" aria-label="Cloud above a ladder"></div><div><h5>The zodiac signs for today, Thursday 17/11</h5><p>1 day ago</p></div></article>
  <article class="side-post" style="top:2739px"><div class="thumb t-cups" role="img" aria-label="Watercolour tea cups"></div><div><h5>Tarot for today, Wednesday 11/16</h5><p>2 day ago</p></div></article>
</section>

<footer>
  <div class="footer-brand">velorimo<i></i></div>
  <nav class="footer-links"><span>Contact</span><span>Charges</span><span>Terms Of Use</span><span>Buy Airtime</span></nav>
  <div class="contact" style="left:165px">
    <div class="ico"><svg width="22" height="28" viewBox="0 0 22 28"><path d="M11 1C5.5 1 1 5.3 1 10.6 1 18 11 27 11 27s10-9 10-16.4C21 5.3 16.5 1 11 1z" fill="none" stroke="#fff" stroke-width="2"/><circle cx="11" cy="10.5" r="3.5" fill="none" stroke="#fff" stroke-width="2"/></svg></div>
    <div>1254 Lorem ipsum dolor sit<br>amet, consectetur - 58452</div>
  </div>
  <div class="divider" style="left:476px"></div>
  <div class="contact" style="left:510px">
    <div class="ico"><svg width="26" height="26" viewBox="0 0 24 24"><path d="M6.6 10.8a15 15 0 006.6 6.6l2.2-2.2c.3-.3.7-.4 1-.2 1.1.4 2.3.6 3.6.6.6 0 1 .4 1 1V20c0 .6-.4 1-1 1A17 17 0 013 4c0-.6.4-1 1-1h3.5c.6 0 1 .4 1 1 0 1.3.2 2.5.6 3.6.1.3 0 .7-.2 1z" fill="#fff"/></svg></div>
    <div><b>Call</b><br>14877</div>
  </div>
  <div class="divider" style="left:758px"></div>
  <div class="contact" style="left:793px;top:3162px">
    <div class="ico" style="margin-top:8px"><svg width="28" height="22" viewBox="0 0 28 22"><rect x="1.5" y="1.5" width="25" height="19" rx="2" fill="none" stroke="#fff" stroke-width="2"/><path d="M2 3l12 9 12-9" fill="none" stroke="#fff" stroke-width="2"/></svg></div>
    <div><b>Email</b><br><b>info@velorimo.gr.com</b></div>
  </div>
  <div class="rule"></div>
  <p class="copyright">© Copyright 2022 velorimo.gr , All Rights Reserved.</p>
</footer>

</div>
</body>
</html>
```